Business Card Design

I need business cards designed for a new company i have started that makes cakes, particularly themed kids cakes with a really modern design and I would like to have my business cards reflect this. I have attached some photos of cakes I have made and would like some to be used.

Industry/Entity Type

Business

Contact Information for Business Card

Business Name: Tarts and Treats by Maren
Mobile: 0492 815 063
email: maren@tartsandtreatsbymaren.example.au
Instagram: instagram.com/tartsandtreatsbymaren/
Facebook: fb.me/tartsandtreatsbymaren

Colors
e667a6
b768aa
3276b5

Requirements
Must have
• Business Name: Tarts and Treats by Maren
• Mobile: 0492 815 063
• email: maren@tartsandtreatsbymaren.example.au
• Instagram: instagram.com/tartsandtreatsbymaren/
• Facebook: fb.me/tartsandtreatsbymaren
Nice to have
• 2 to 3 pictures of my cakes

```html
<!DOCTYPE html>
<html lang="en">
<head>
<meta charset="utf-8">
<title>Tarts and Treats by Maren — Business Card</title>
<link rel="stylesheet" href="https://fonts.googleapis.com/css2?family=PT+Sans:wght@400;700&display=swap">
<style>
  :root {
    --pink: #e667a6;
    --orchid: #b768aa;
    --blue: #3276b5;
    --paper: #ffffff;
    --ink: #4a4a4a;
    --muted: #9a9a9a;
    --stage: #eeebe6;
    --blush: #f6eef5;
  }
  * { box-sizing: border-box; margin: 0; padding: 0; }
  html, body {
    width: 1200px; height: 950px; overflow: hidden;
    background: var(--stage);
    font-family: "PT Sans", sans-serif;
  }
  .canvas {
    width: 1200px; height: 950px;
    display: flex; flex-direction: column; align-items: center; justify-content: center;
    gap: 50px;
  }
  .card {
    position: relative;
    width: 700px; height: 400px;
    border-radius: 6px;
    box-shadow: 0 10px 30px rgba(0,0,0,.15);
    overflow: hidden;
  }
  .card--front { background: var(--paper); }
  .card--back { background: var(--pink); }

  .brand-mark {
    position: absolute;
    border-radius: 50%;
    display: flex; flex-direction: column; align-items: center; justify-content: center;
    text-align: center;
    font-weight: 700;
    line-height: 1.05;
  }
  .card--front .brand-mark {
    width: 310px; height: 310px; right: 40px; top: 24px;
    background: var(--blush);
    border: 4px solid var(--pink);
    color: var(--orchid);
    font-size: 46px;
  }
  .card--back .brand-mark {
    width: 250px; height: 250px; left: 225px; top: 75px;
    background: var(--paper);
    color: var(--pink);
    font-size: 36px;
  }
  .brand-mark .by { font-size: .62em; margin-top: 10px; }

  .contact {
    position: absolute; left: 44px; bottom: 40px;
    color: var(--ink);
  }
  .contact__name {
    color: var(--pink); font-size: 24px; font-weight: 400;
    letter-spacing: .5px; text-transform: uppercase;
  }
  .contact__role { color: var(--pink); font-size: 17px; margin-bottom: 16px; }
  .contact__list { list-style: none; }
  .contact__list li {
    display: flex; align-items: center; gap: 12px;
    font-size: 16px; line-height: 1.75;
  }
  .contact__icon { width: 16px; height: 16px; flex: none; }
</style>
</head>
<body>
<main class="canvas">
  <section class="card card--front" aria-label="Business card front">
    <div class="brand-mark">
      <span>Tarts and<br>Treats</span>
      <span class="by">by Maren</span>
    </div>
    <div class="contact">
      <p class="contact__name">Jonah Whitby</p>
      <p class="contact__role">CEO/Founder</p>
      <ul class="contact__list">
        <li>
          <svg class="contact__icon" viewBox="0 0 16 16" aria-hidden="true">
            <rect x="3.5" y="1" width="9" height="14" rx="1.5" fill="none" stroke="var(--muted)" stroke-width="1.5"/>
            <circle cx="8" cy="12.5" r="0.9" fill="var(--muted)"/>
          </svg>
          0492 815 063
        </li>
        <li>
          <svg class="contact__icon" viewBox="0 0 16 16" aria-hidden="true"><rect x="1" y="1" width="14" height="14" rx="2" fill="var(--muted)"/></svg>
          tartsandtreatsbymaren
        </li>
        <li>
          <svg class="contact__icon" viewBox="0 0 16 16" aria-hidden="true"><rect x="1" y="1" width="14" height="14" rx="2" fill="var(--muted)"/></svg>
          tartsandtreatsbymaren
        </li>
        <li>
          <svg class="contact__icon" viewBox="0 0 16 16" aria-hidden="true">
            <rect x="1" y="3" width="14" height="10" rx="1" fill="none" stroke="var(--muted)" stroke-width="1.5"/>
            <path d="M1.5 3.5 8 9l6.5-5.5" fill="none" stroke="var(--muted)" stroke-width="1.5"/>
          </svg>
          maren@tartsandtreatsbymaren.example.au
        </li>
      </ul>
    </div>
  </section>

  <section class="card card--back" aria-label="Business card back">
    <div class="brand-mark">
      <span>Tarts and<br>Treats</span>
      <span class="by">by Maren</span>
    </div>
  </section>
</main>
</body>
</html>
```